Sleek wordpress site for Bramblecrest finishing works

We are a commercial job shop that serves B2B, govt & LEO and retail clients.We need a wordpress site with 6 individual pages: homepage, coating, laser engraving, laser cutting, part marking, and contact us. I have attached an outline of the desired flow and sub headings for each page. I would like to incorporate the colors of the logo through out the site to be clean and sleek enough to appeal to B2B commercial clients yet be inviting enough for retail clients.

I would like to have easy picture functionality so photographs on each page can be updated easily.

Target Market(s)

B2B industrial & Govt and Military part marking, laser engraving and coating: machine shops, aerospace companies, tool manufactures. Retail: personalized gifts, Job Shop

Coding

Coded - Design and coding required

Font styles to use
Sans Serif
Other font styles liked:
• Open to suggestion

Colors
0255a3
3176b5
eaf1f7
cfdeed
ffffff

Requirements
Must have
• Clean easy to navigate flow, separate pages as indicated on attached outline, high class feel. Great picture functionality, professional and inviting feel,
• **update: needs to be optimized for mobile, should have a gallery function. Gallery can be an additional page or embedded
Nice to have
• Social media connectivity links,
Should not have
• crappy plugins that make back-end management difficult, no blog

```html
<!DOCTYPE html>
<html lang="en">
<head>
<meta charset="utf-8">
<title>Bramblecrest Finishing Works</title>
<link rel="stylesheet" href="https://fonts.googleapis.com/css2?family=Open+Sans:wght@400;600;700;800&display=swap">
<style>
:root{
  --blue:#0255a3;
  --blue-mid:#3176b5;
  --blue-pale:#eaf1f7;
  --blue-soft:#cfdeed;
  --white:#ffffff;
  --ink:#222222;
  --text:#555555;
  --footer:#ececec;
}
*{box-sizing:border-box;margin:0;padding:0}
html,body{width:1200px;height:3536px;overflow:hidden}
body{font-family:"Open Sans",sans-serif;color:var(--ink);background:var(--white);position:relative}
section,header,footer{position:absolute;left:0;width:1200px}
.btn{display:inline-flex;align-items:center;justify-content:center;background:var(--blue);color:var(--white);font-weight:700;font-size:17px;border-radius:26px;text-decoration:none;letter-spacing:.5px}
.photo{position:absolute}

/* header */
.site-header{top:0;height:100px;background:var(--white);z-index:5;box-shadow:0 2px 6px rgba(0,0,0,.08)}
.nav{position:absolute;top:54px;display:flex;gap:26px;font-size:15px;font-weight:600;color:#333;text-transform:uppercase}
.nav-left{left:122px}
.nav-right{right:96px;align-items:center}
.call{position:absolute;top:18px;right:98px;font-size:15px;color:#444;display:flex;align-items:center;gap:8px}
.call b{color:var(--blue);font-weight:700}
.brand-disc{position:absolute;left:512px;top:-70px;width:176px;height:216px;border-radius:0 0 88px 88px;background:var(--white);display:flex;align-items:flex-end;justify-content:center;padding-bottom:60px}
.brand-name{font-size:15px;font-weight:700;color:var(--blue);text-align:center;line-height:1.25;text-transform:uppercase}

/* hero */
.hero{top:100px;height:540px;overflow:hidden}
.hero .photo{inset:0;background:linear-gradient(120deg,#3a3f45 0%,#565c63 40%,#2a2e33 70%,#6a5a4a 100%)}
.hero-copy{position:absolute;top:165px;width:100%;text-align:center;color:var(--white)}
.hero-copy h1{font-size:55px;font-weight:800;letter-spacing:1px;text-shadow:0 2px 6px rgba(0,0,0,.4)}
.hero-copy p{font-size:19px;font-weight:600;margin-top:6px}
.hero-copy .btn{width:166px;height:46px;margin-top:30px;font-weight:600}
.dots{position:absolute;top:466px;left:568px;display:flex;gap:5px}
.dots span{width:9px;height:9px;border-radius:50%;border:1.5px solid var(--white)}
.dots span:first-child{background:var(--white)}
.hero svg{position:absolute;left:0;bottom:0}

/* about */
.about{top:740px;height:300px}
.about .photo{left:99px;top:0;width:471px;height:294px;background:linear-gradient(135deg,#2c2f33,#4a4d52 55%,#7a5a3a);outline:2px solid #222}
.about-copy{position:absolute;left:601px;top:0;width:504px}
.about-copy h2{font-size:31px;font-weight:800}
.about-copy p{font-size:13px;line-height:2;color:var(--text);margin-top:8px;text-align:justify}
.about-copy .btn{width:138px;height:46px;margin-top:16px;font-size:16px}

/* statement band */
.statement{top:1134px;height:334px;background:linear-gradient(90deg,#15191d,#2b3035 50%,#191d21)}
.statement h2{position:absolute;top:80px;width:100%;text-align:center;color:var(--white);font-size:30px;font-weight:700;line-height:54px;text-transform:uppercase}
.statement .btn{position:absolute;left:527px;top:210px;width:148px;height:44px;font-size:16px}

/* materials */
.materials{top:1530px;height:470px}
.materials h2{text-align:center;font-size:30px;font-weight:800;margin-top:10px}
.card{position:absolute;top:84px;width:238px}
.card .photo{position:relative;width:238px;height:201px}
.card h3{font-size:19px;font-weight:700;margin-top:26px;text-transform:uppercase}
.card p{font-size:13px;line-height:1.9;color:var(--text);margin-top:6px}
.card a{display:block;font-size:12px;font-weight:700;color:var(--blue);margin-top:10px;text-transform:uppercase;text-decoration:none}

/* cta */
.cta{top:2062px;height:335px;background:linear-gradient(100deg,var(--blue),var(--blue-mid) 55%,var(--blue))}
.cta h2{position:absolute;top:68px;width:100%;text-align:center;color:var(--white);font-size:29px;font-weight:700;line-height:48px;text-transform:uppercase}
.cta p{position:absolute;top:180px;width:100%;text-align:center;color:var(--white);font-size:21px;font-weight:700}
.cta .btn-outline{position:absolute;left:542px;top:230px;width:116px;height:44px;border:2px solid var(--white);border-radius:24px;color:var(--white);font-weight:700;font-size:16px;display:flex;align-items:center;justify-content:center}

/* newsletter */
.newsletter{top:2470px;height:230px;text-align:center}
.newsletter h2{font-size:31px;font-weight:800}
.newsletter p{font-size:24px;color:#444;line-height:36px;margin-top:6px}
.signup{position:absolute;left:349px;top:146px;display:flex}
.signup span{width:370px;height:40px;border:1px solid #bbb;font-size:13px;color:#555;display:flex;align-items:center;padding-left:18px}
.signup b{width:130px;height:40px;background:var(--blue);color:var(--white);font-size:15px;display:flex;align-items:center;justify-content:center}

/* gallery */
.gallery{top:2744px;height:470px}
.gallery .btn{position:absolute;left:527px;top:392px;width:146px;height:48px;font-size:16px}

/* footer */
.site-footer{top:3253px;height:283px;background:var(--footer)}
.footer-brand{position:absolute;top:70px;width:100%;text-align:center}
.footer-brand .brand-name{font-size:24px}
.address{position:absolute;top:184px;width:100%;text-align:center;font-size:13px;color:#333;display:flex;justify-content:center;gap:6px;align-items:center}
.footer-bar{position:absolute;left:99px;right:99px;top:230px;border-top:1px solid #cfcfcf;display:flex;justify-content:space-between;align-items:center;padding-top:16px;font-size:13px;color:#333}
.social{display:flex;gap:16px}
.social span{width:16px;height:16px;border-radius:50%;background:var(--blue)}
</style>
</head>
<body>

<header class="site-header">
  <nav class="nav nav-left"><span>Home</span><span>Coating</span><span>Laser Engraving</span></nav>
  <div class="brand-disc"><div class="brand-name">Bramblecrest<br>Finishing Works</div></div>
  <div class="call">
    <svg width="14" height="14" viewBox="0 0 24 24"><path fill="#0255a3" d="M6.6 10.8a15.1 15.1 0 0 0 6.6 6.6l2.2-2.2c.3-.3.7-.4 1-.2 1.1.4 2.3.6 3.6.6.6 0 1 .4 1 1V20c0 .6-.4 1-1 1A17 17 0 0 1 3 4c0-.6.4-1 1-1h3.5c.6 0 1 .4 1 1 0 1.3.2 2.5.6 3.6.1.3 0 .7-.2 1z"/></svg>
    <span><b>CALL US</b> : 555.014.2290</span>
  </div>
  <nav class="nav nav-right"><span>Laser Cutting</span><span>Part Marking</span><span>Contact Us</span>
    <svg width="15" height="15" viewBox="0 0 24 24"><circle cx="10" cy="10" r="7" fill="none" stroke="#333" stroke-width="3"/><line x1="15" y1="15" x2="22" y2="22" stroke="#333" stroke-width="3"/></svg>
  </nav>
</header>

<section class="hero">
  <div class="photo" role="img" aria-label="Laser cutting head slicing patterned shapes from a metal sheet"></div>
  <div class="hero-copy">
    <h1>PRECISION FINISHING</h1>
    <p>Give us a call for a helpful, efficient and friendly service</p>
    <a class="btn">READ MORE</a>
  </div>
  <div class="dots"><span></span><span></span><span></span><span></span></div>
  <svg width="1200" height="80" viewBox="0 0 1200 80"><path d="M0 20 Q600 60 1200 20 L1200 80 L0 80Z" fill="#ffffff"/><path d="M0 20 Q600 60 1200 20 L1200 30 Q600 72 0 30Z" fill="#0255a3"/></svg>
</section>

<section class="about">
  <div class="photo" role="img" aria-label="Laser cutter nozzle throwing sparks over a steel plate"></div>
  <div class="about-copy">
    <h2>ABOUT US</h2>
    <p>Veritek is a spray on ceramic based finish that can be applied to metals, plastics, polymers &amp; wood. The unique formulation used for Veritek ceramic coating enhances a number of physical performance properties including abrasion/wear resistance, corrosion resistance, chemical resistance, impact strength, &amp; hardness.</p>
    <p>Veritek ceramic coatings utilize state-of-the-art technology to out-perform any competitive coating in both laboratory settings and real world applications, making it ideal for firearm finishes.</p>
    <a class="btn">READ MORE</a>
  </div>
</section>

<section class="statement" role="img" aria-label="Dark background of a laser machine at work">
  <h2>Ceramic coatings utilize state-of-the-art<br>technology to out-perform any competitive coating</h2>
  <a class="btn">CONTACT US</a>
</section>

<section class="materials">
  <h2>OUR MATERIALS</h2>
  <article class="card" style="left:99px">
    <div class="photo" role="img" aria-label="Laser engraving head with red glow" style="background:linear-gradient(135deg,#d9dde2,#b6252c 60%,#5a5f66)"></div>
    <h3>Laser Engraving</h3>
    <p>With our selection of CO2 and fiber lasers there are very few materials &amp; substrates that we cannot mark or engrave...</p>
    <a>Read More</a>
  </article>
  <article class="card" style="left:354px">
    <div class="photo" role="img" aria-label="Laser cutter sparking over a perforated sheet" style="background:linear-gradient(135deg,#3b3f44,#7d7f82 50%,#c8944e)"></div>
    <h3>Laser Cutting</h3>
    <p>Bramblecrest can custom cut virtually any shape or design in a variety of substrates/materials. Cutting area of our CO2 laser is 24" X 18".</p>
    <a>Read More</a>
  </article>
  <article class="card" style="left:610px">
    <div class="photo" role="img" aria-label="Yellow and red part marking machine" style="background:linear-gradient(135deg,#2e3136,#e0b21c 45%,#c2262b 70%,#3a3d42)"></div>
    <h3>Part Marking</h3>
    <p>Every part we mark carries a clean, lasting code or logo, built to hold up in the shop and on the industry's toughest jobs.</p>
    <a>Read More</a>
  </article>
  <article class="card" style="left:865px">
    <div class="photo" role="img" aria-label="Coating equipment under blue light" style="background:linear-gradient(135deg,#9a2a35,#c7cbd1 45%,#5a62b8 70%,#3a3d42)"></div>
    <h3>Coatings</h3>
    <p>Veritek ceramic coatings utilize state-of-the-art technology to out-perform any competitive coating in real world...</p>
    <a>Read More</a>
  </article>
</section>

<section class="cta" role="img" aria-label="Blue toned background of a cutting machine">
  <h2>Tie up with Veritek and making metals,<br>plastics, polymers &amp; wood ideal for firearm finishes.</h2>
  <p>Talk To Our Team !!</p>
  <a class="btn-outline">HIRE US</a>
</section>

<section class="newsletter">
  <h2>JOIN OUR NEWSLETTER</h2>
  <p>Sign up for our newsletter and get 20%<br>off your next Service.</p>
  <div class="signup"><span>Enter your Email</span><b>SUBSCRIBE</b></div>
</section>

<section class="gallery">
  <div class="photo" role="img" aria-label="Sparks flying from a laser cutting perforated metal" style="left:99px;top:0;width:626px;height:363px;background:linear-gradient(135deg,#2d3136,#6f7479 45%,#d0a060 70%,#3a3e43)"></div>
  <div class="photo" role="img" aria-label="Laser cutting machine bed in blue and orange light" style="left:733px;top:0;width:370px;height:177px;background:linear-gradient(135deg,#243a66,#b35a3a 55%,#2a2f36)"></div>
  <div class="photo" role="img" aria-label="Laser head cutting a glowing gold sheet" style="left:733px;top:186px;width:370px;height:177px;background:linear-gradient(135deg,#3a2a1c,#c88a2a 55%,#2a1e16)"></div>
  <a class="btn">VIEW ALL</a>
</section>

<footer class="site-footer">
  <div class="footer-brand"><div class="brand-name">Bramblecrest<br>Finishing Works</div></div>
  <div class="address">
    <svg width="11" height="15" viewBox="0 0 12 16"><path fill="#0255a3" d="M6 0a6 6 0 0 0-6 6c0 4.5 6 10 6 10s6-5.5 6-10a6 6 0 0 0-6-6zm0 8.5A2.5 2.5 0 1 1 6 3.5a2.5 2.5 0 0 1 0 5z"/></svg>
    <span>418 Harlow Lane #7, Fenwick, OR 97114</span>
  </div>
  <div class="footer-bar">
    <span>Copyright © 2018.&nbsp; All Rights Reserved</span>
    <div class="social"><span></span><span></span><span></span></div>
  </div>
</footer>

</body>
</html>
```